Wordpress website re-design

Update existing 5 page wordpress website to look more professional. We run a 10 week boxing program that ends in a black tie gala event.

We would like to keep the existing pink hero colour.

The website:
- must be Wordpress
- prefer it to work with the Elementor plugin for easy future changes
- Keep the existing URL structure
- Use white space/backgrounds - D not want all black background or the pink colour used as the background for an entire section
- Shouldn't look too 'templatey'. Good flow between sections

Logo, images and video to use can be found here: https://files.qorvanshare.net/folders/8kq3ZtLmWpe2RxvBn7HsYcDa4-Tu?usp=sharing

Website to be redesigned: https://punchforpurpose-example.com.au/

Target Market(s)

Men working office jobs aged 28-38

Coding

Coded - Design and coding required

Number of Pages Required

5+ page

Colors

Designer to choose colors to be used in the design.

Requirements
Must have
• Wordpress
Nice to have
• Work with Elementor so that I can easily make changes in the future
Should not have
• Entirely black background. Want it to be lighter / plenty of white background. Not too blocky - flowing through sections and some of the images with backgrounds removed to make it less blocky also. I do not want it to be clerly 'templatey'. The pink should be used as a hero colour, not for entire sections

```html
<!DOCTYPE html>
<html lang="en">
<head>
<meta charset="utf-8">
<title>Punch for Purpose</title>
<link rel="stylesheet" href="https://fonts.googleapis.com/css2?family=Nunito:ital,wght@0,400;0,600;0,700;1,400&display=swap">
<style>
:root{
  --pink:#f0047f;
  --pink-soft:#fcc0e6;
  --navy:#1d1a7a;
  --ink:#1c1c1c;
  --grey:#6d6d6d;
  --page:#f8f8f8;
  --white:#ffffff;
}
*{box-sizing:border-box;margin:0;padding:0}
html,body{width:1200px;height:2963px;overflow:hidden}
body{position:relative;background:var(--page);font-family:"Nunito",sans-serif;color:var(--ink)}
.abs{position:absolute}
.btn{position:absolute;display:flex;align-items:center;justify-content:center;background:var(--pink);color:var(--white);border-radius:3px;font-size:15px}
.brand{display:flex;align-items:center;gap:8px;font-weight:700;color:var(--pink);font-size:18px;white-space:nowrap}
.brand .dot{width:14px;height:14px;background:var(--pink)}

/* header */
.site-header{left:0;top:0;width:1200px;height:131px;background:var(--page)}
.site-header .brand{position:absolute;left:83px;top:52px}
.main-nav{position:absolute;left:455px;top:55px;display:flex;gap:34px;font-size:17px}
.site-header .btn{left:1007px;top:44px;width:109px;height:44px;font-size:17px;border-radius:4px}

/* hero */
.hero{left:0;top:131px;width:1200px;height:611px;background:radial-gradient(ellipse at 62% 30%,#5a5f66 0%,#2a2d31 40%,#111214 100%)}
.hero h1{position:absolute;left:84px;top:180px;font-size:47px;font-weight:600;line-height:64px;color:var(--white)}
.hero p{position:absolute;left:84px;top:322px;font-size:19px;line-height:27px;color:var(--white)}
.hero .join{left:85px;top:394px;width:102px;height:41px}
.hero .watch{position:absolute;left:206px;top:394px;width:135px;height:41px;border:1px solid var(--pink);color:var(--pink);display:flex;align-items:center;justify-content:center;gap:6px;font-size:15px}

.event-card{left:639px;top:456px;width:363px;height:389px;background:var(--white);box-shadow:0 4px 14px rgba(0,0,0,.12);text-align:center}
.event-card h2{font-size:28px;font-weight:600;margin-top:15px}
.event-card h3{font-size:22px;font-weight:400;line-height:31px}
.event-card .date{font-size:17px;margin:12px 0 16px}
.event-card .btn{left:112px;top:315px;width:138px;height:35px;font-size:17px}

/* about */
.about-photo{left:0;top:928px;width:639px;height:412px;border-radius:0 8px 8px 0;background:linear-gradient(135deg,#2b2a2e 0%,#5a4a48 45%,#a33a3a 55%,#2c2b30 100%)}
.about{left:695px;top:975px;width:390px}
.about h2,.section-title{color:var(--pink);font-size:27px;font-weight:600}
.about p{margin-top:22px;font-style:italic;font-size:13px;line-height:19px;color:var(--grey)}
.perks{display:grid;grid-template-columns:222px 150px;row-gap:15px;margin-top:18px;list-style:none;font-style:italic;font-size:13px;color:var(--grey)}
.perks li::before{content:"✕";color:var(--pink);margin-right:7px;font-style:normal}
.perks li.wide{grid-column:1 / 3}
.about .btn{position:relative;margin-top:24px;width:113px;height:40px;font-size:14px}

/* cost */
.section-title{position:absolute;left:0;width:1200px;text-align:center}
.acc{background:var(--white);width:292px;padding:0 12px}
.acc .row{display:flex;justify-content:space-between;align-items:center;height:56px;font-size:17px;font-weight:600}
.acc .row span.sign{color:#cfcfcf;font-weight:400;font-size:26px}
.acc p{font-size:10px;line-height:15px;color:var(--grey);padding-bottom:16px}
.price{left:800px;top:1497px;width:237px;height:346px;background:var(--white);box-shadow:0 3px 12px rgba(0,0,0,.1);text-align:center}
.price .head{background:#f4f4f4;height:82px;padding-top:14px}
.price .head h3{color:var(--pink);font-size:23px;font-weight:600}
.price .head small{color:var(--pink);font-size:11px}
.price .amount{font-size:22px;font-weight:700;margin-top:16px}
.price .once{font-size:10px}
.price ul{list-style:none;margin:12px 20px 0;font-size:10px}
.price li{padding:9px 0;border-bottom:1px solid #eee}
.price li::after{content:" ✓";color:var(--pink)}
.price .btn{left:68px;top:290px;width:113px;height:36px}
.note{left:0;width:1200px;top:1866px;text-align:center;font-size:10px;font-style:italic;color:var(--grey)}
.note b{font-weight:700}

/* where */
.venue{text-align:center;width:480px}
.venue h3{color:var(--pink);font-size:22px;font-weight:600}
.venue p{font-size:16px;line-height:23px;margin-top:14px}
.map{width:482px;height:309px;background:linear-gradient(160deg,#e8ecef 0%,#d9e6d7 50%,#c9d9ec 100%)}

/* cta */
.cta{left:0;top:2570px;width:1200px;height:157px;background:var(--pink-soft)}
.cta h2{position:absolute;left:84px;top:40px;font-size:40px;font-weight:700;color:var(--navy)}
.cta p{position:absolute;left:84px;top:94px;font-size:22px;color:var(--navy)}
.cta .btn{left:816px;top:56px;width:183px;height:50px;font-size:16px;border-radius:5px}

/* footer */
.site-footer .brand{position:absolute;left:0;width:1200px;top:2770px;justify-content:center}
.foot-nav{left:0;width:1200px;top:2826px;display:flex;justify-content:center;gap:23px;font-size:14px}
.socials{left:943px;top:2877px;display:flex;gap:14px}
.socials span{width:13px;height:13px;border-radius:50%;background:#c9c9c9}
.rule{left:117px;top:2905px;width:965px;height:1px;background:#cfcfcf}
.copy{left:0;width:1200px;top:2928px;text-align:center;font-size:10px;color:#c9a8bd}
</style>
</head>
<body>

<header class="abs site-header">
  <div class="brand"><span class="dot"></span>Punch for Purpose</div>
  <nav class="main-nav"><span>Home</span><span>About The Program</span><span>Our Services</span><span>Meet The Team</span></nav>
  <span class="btn">Contact Us</span>
</header>

<section class="abs hero" role="img" aria-label="Boxer walking toward a lit ring in a dark arena">
  <h1>From desk to the<br>ring in 10 weeks</h1>
  <p>Lorem ipsum dolor sit amet purus<br>consectetur. Suscipit purus.</p>
  <span class="btn join">Join Now</span>
  <span class="watch">Watch Video
    <svg width="9" height="10" viewBox="0 0 9 10"><path d="M0 0 9 5 0 10z" fill="#f0047f"/></svg>
  </span>
</section>

<aside class="abs event-card">
  <h2>Upcoming Event</h2>
  <h3 style="margin-top:14px">Riverside Music hall<br>day event</h3>
  <div class="date">13 Feb 2024 - 20 April 2024</div>
  <h3>Grand Harbour Convention<br>Centre night event</h3>
  <div class="date">2 April 2024 - 15 June 2024</div>
  <span class="btn">Join Now</span>
</aside>

<div class="abs about-photo" role="img" aria-label="Boxer in red entering the arena between sparklers"></div>
<section class="abs about">
  <h2>What is Punch for Purpose?</h2>
  <p>Punch for Purpose is a 10 Week Program, raising much needed funds for charity, whilst providing everyday people the experience of stepping into a boxing ring in front of a packed arena with friends, family and colleagues cheering you on!</p>
  <ul class="perks">
    <li>Lose weight and get fit.</li><li>Learn boxing skills.</li>
    <li>Supporting charity.</li><li>Build Friendship.</li>
    <li class="wide">Fight in front of friend, family and coworkers.</li>
  </ul>
  <span class="btn">Join Now</span>
</section>

<h2 class="section-title" style="top:1425px">What’s the Cost?</h2>
<div class="abs acc" style="left:162px;top:1517px"><div class="row">10 Weeks training Session<span class="sign">−</span></div><p>Lorem ipsum dolor sit amet Mobi consectetur. malesuada Mobi nula lorem vivamus senectus comodo purus malesuada Mobi nula.</p></div>
<div class="abs acc" style="left:474px;top:1517px"><div class="row">Fight Kit<span class="sign">+</span></div></div>
<div class="abs acc" style="left:162px;top:1675px"><div class="row">Member Northgate Boxing<span class="sign">+</span></div></div>
<div class="abs acc" style="left:474px;top:1675px"><div class="row">World Class Trainer<span class="sign">+</span></div></div>
<div class="abs acc" style="left:162px;top:1766px"><div class="row">Black Tie Fight Event<span class="sign">+</span></div></div>
<div class="abs acc" style="left:474px;top:1766px"><div class="row">Fair Matchmaking<span class="sign">+</span></div></div>

<div class="abs price">
  <div class="head"><h3>10 Week program</h3><small>Pay up front</small></div>
  <div class="amount">$ 895</div>
  <div class="once">Once off</div>
  <ul><li>10 Weeks of training</li><li>Fight kit</li><li>Amateur fight</li><li style="border:0">Membership to Northgate boxing</li></ul>
  <span class="btn">Join Now</span>
</div>
<p class="abs note"><b>Note:</b> Each fighter is responsible for selling 20 tickets for the boxing event</p>

<h2 class="section-title" style="top:1966px">Where is it?</h2>
<div class="abs venue" style="left:97px;top:2040px"><h3>Your Training Place</h3><p>Northgate Boxing – 42 Example Road,<br>Hillside</p></div>
<div class="abs venue" style="left:622px;top:2040px"><h3>Black Tie Event</h3><p>Riverside Music Hall – 210-216<br>Sample St, Valley Heights</p></div>
<div class="abs map" style="left:96px;top:2157px" role="img" aria-label="Street map of the training venue"></div>
<div class="abs map" style="left:621px;top:2157px" role="img" aria-label="Street map of the black tie event venue"></div>

<section class="abs cta">
  <h2>Got Any Question?</h2>
  <p>Drop us a line and keep in touch with us!</p>
  <span class="btn">Contact Us Now!</span>
</section>

<footer class="site-footer">
  <div class="brand"><span class="dot"></span>Punch for Purpose</div>
  <nav class="abs foot-nav"><span>Home</span><span>About The Program</span><span>Our Services</span><span>Meet The Team</span><span>Contact Us</span></nav>
  <div class="abs socials"><span></span><span></span><span></span><span></span><span></span></div>
  <div class="abs rule"></div>
  <p class="abs copy">Copyright © 2023 - Punch for Purpose - All rights reserved</p>
</footer>

</body>
</html>
```